Valdane Companies Business Card Design

We need a new business card for our Private Equity Real Estate Development firm, “Valdane” and our EB-5 regional center “Thornmere Regional Center” on one card. We prefer a design that is simple, elegant, and represents the luxury products we design and build as well as the financial security and stability our successful history has produced. We are an industry leader in our field and 3rd generation family business that has evolved into an institutional quality investment platform. Considered design size is standard business card dimensions (3.5 x 2 inches with an additional 1/8 inch space for design elements or backgrounds that extend beyond the finished size of your piece.

Target Market(s)

• High net worth individuals
• Highly skilled technical workers and physicians in the US seeking investment-based immigration opportunities
• Sophisticated private equity investors
• Intermediary partners include domestic attorneys and investment brokers, as well as international agent networks
• US real estate developers

Industry/Entity Type

Finance

Contact Information for Business Card

(Providing placeholder info for personal information, please design for longer character spaces, longer names and addresses etc..)
• Logo for Valdane
• Logo for Thornmere Regional Center
• Full name: Marcus Valdane
• Job title: CEO
• Email address: mvaldane@valdanecompanies.com
• Cell phone number: +1.555.314.2287
• Office number +1.555.628.4410
• Office address: Larkfield Court 5, 4817 Vista Orilla, Ashbury Vale, OR.
• Website: www.valdanecompanies.com

Font styles to use
Serif
Sans Serif

Colors
ec1f27
ffffff
000000

Requirements
Must have
• • Logo for Valdane
• • Logo for Thornmere Regional Center
• - Use rounded corners
• (See .ai file included for logos)
Nice to have
• • Simple, elegant design
• • Aesthetically compatible with our website design (www.valdanecompanies.com)
• • Color palette including but not limited to white, black, and red (as per logos)
Should not have
• - Not too much red color
• - Do not stack both logos on top of each other

```html
<!DOCTYPE html>
<html lang="en">
<head>
<meta charset="utf-8">
<title>Valdane Companies Business Card</title>
<link href="https://fonts.googleapis.com/css2?family=Libre+Baskerville:wght@400;700&family=Open+Sans:wght@400;600&display=swap" rel="stylesheet">
<style>
  :root {
    --brand-red: #a51c30;
    --ink: #1a1a1a;
    --card-black: #0d0d0d;
    --logo-grey: #3c3c3c;
    --paper: #ffffff;
    --backdrop: #3a3a3a;
    --band-dark: #2a2a2a;
  }
  html, body {
    margin: 0;
    width: 1200px;
    height: 1000px;
    overflow: hidden;
    background: var(--backdrop);
  }
  .stage {
    position: relative;
    width: 1200px;
    height: 1000px;
  }
  .card {
    position: absolute;
    left: 250px;
    width: 700px;
    height: 400px;
    border-radius: 24px;
    overflow: hidden;
  }
  .card--back {
    top: 60px;
    background: var(--card-black);
  }
  .card--front {
    top: 520px;
    background: var(--paper);
  }

  /* Back side */
  .back-brand {
    position: absolute;
    top: 0;
    height: 400px;
    display: flex;
    align-items: center;
    justify-content: center;
    font-family: "Libre Baskerville", serif;
    font-weight: 700;
  }
  .back-brand--valdane {
    left: 0;
    width: 340px;
    color: var(--logo-grey);
    font-size: 30px;
    letter-spacing: 1px;
  }
  .back-brand--thornmere {
    left: 360px;
    width: 340px;
    color: var(--brand-red);
    font-size: 24px;
    line-height: 1.25;
    text-align: center;
  }
  .back-divider {
    position: absolute;
    left: 349px;
    top: 120px;
    width: 2px;
    height: 160px;
    background: var(--brand-red);
  }

  /* Front side */
  .front-brand {
    position: absolute;
    left: 30px;
    top: 150px;
    width: 290px;
    text-align: center;
    font-family: "Libre Baskerville", serif;
    font-weight: 700;
    font-size: 32px;
    color: var(--ink);
    letter-spacing: 1px;
  }
  .front-divider {
    position: absolute;
    left: 340px;
    top: 95px;
    width: 2px;
    height: 190px;
    background: var(--brand-red);
  }
  .contact {
    position: absolute;
    left: 358px;
    top: 90px;
    font-family: "Libre Baskerville", serif;
    color: var(--ink);
  }
  .contact__name {
    margin: 0;
    font-size: 19px;
    font-weight: 700;
    color: var(--brand-red);
    letter-spacing: 0.5px;
  }
  .contact__title {
    margin: 2px 0 12px;
    font-family: "Open Sans", sans-serif;
    font-size: 11px;
    color: var(--ink);
  }
  .contact__address {
    margin: 0 0 2px;
    font-size: 13px;
    line-height: 1.35;
  }
  .contact__line {
    display: flex;
    align-items: center;
    gap: 6px;
    font-size: 13px;
    line-height: 1.4;
  }
  .contact__icon {
    width: 11px;
    height: 11px;
    flex: none;
  }
  .contact__accent { color: var(--brand-red); }
  .wave {
    position: absolute;
    left: 0;
    top: 0;
    width: 700px;
    height: 400px;
  }
</style>
</head>
<body>
<main class="stage">

  <section class="card card--back" aria-label="Card back">
    <div class="back-brand back-brand--valdane">Valdane Capital</div>
    <div class="back-divider"></div>
    <div class="back-brand back-brand--thornmere">Thornmere<br>Regional Center</div>
  </section>

  <section class="card card--front" aria-label="Card front">
    <svg class="wave" viewBox="0 0 700 400" aria-hidden="true">
      <path d="M0,290 C160,285 320,335 470,372 C570,396 650,402 700,398 L700,400 L0,400 Z" fill="var(--band-dark)"/>
      <path d="M0,296 C160,291 320,341 470,378 C570,402 650,408 700,404 L700,410 L0,410 Z" fill="var(--paper)"/>
      <path d="M0,301 L0,400 L700,400 L700,398 C600,405 540,400 470,383 C320,346 160,296 0,301 Z" fill="var(--brand-red)"/>
    </svg>

    <div class="front-brand">Valdane Capital</div>
    <div class="front-divider"></div>

    <div class="contact">
      <p class="contact__name">MARCUS VALDANE</p>
      <p class="contact__title">CEO</p>
      <p class="contact__address">Larkfield Court 5, 4817<br>Vista Orilla, Ashbury Vale, OR.</p>
      <div class="contact__line">
        <svg class="contact__icon" viewBox="0 0 12 12" aria-hidden="true"><circle cx="6" cy="6" r="6" fill="var(--brand-red)"/><path d="M3.5,3 L5,3 L5.5,4.6 L4.7,5.2 Q5.4,6.7 6.8,7.3 L7.4,6.5 L9,7 L9,8.5 Q5,9 3.5,4.5 Z" fill="#fff"/></svg>
        <span>+1.555.314.2287</span>
      </div>
      <div class="contact__line">
        <svg class="contact__icon" viewBox="0 0 12 12" aria-hidden="true"><rect x="0" y="0" width="12" height="12" rx="2" fill="var(--brand-red)"/><rect x="4" y="2.5" width="4" height="7" rx="0.8" fill="#fff"/></svg>
        <span>+1.555.628.4410</span>
      </div>
      <div class="contact__line">
        <svg class="contact__icon" viewBox="0 0 12 12" aria-hidden="true"><rect x="0" y="0" width="12" height="12" rx="2" fill="var(--brand-red)"/><path d="M2.5,3.5 H9.5 V8.5 H2.5 Z M2.5,3.5 L6,6.3 L9.5,3.5" fill="none" stroke="#fff" stroke-width="0.9"/></svg>
        <span>mvaldane@valdanecompanies.com</span>
      </div>
      <div class="contact__line">
        <svg class="contact__icon" viewBox="0 0 12 12" aria-hidden="true"><circle cx="6" cy="6" r="6" fill="var(--brand-red)"/><circle cx="6" cy="6" r="3.6" fill="none" stroke="#fff" stroke-width="0.8"/><path d="M2.4,6 H9.6 M6,2.4 V9.6" stroke="#fff" stroke-width="0.8"/></svg>
        <span>www.<span class="contact__accent">valdanecompanies</span>.com</span>
      </div>
    </div>
  </section>

</main>
</body>
</html>
```